IT Company that provides secure IT solutions and services to our customers

We need business cards and a logo for a new IT Solutions company just created based in Kuala Lumpur, Malaysia. But will also be serving other countries in the region. We provide secure data, voice solutions on mobile platforms. Our first offering is encrypted voice and data solutions for IOS, Android, Windows and BlackBerry devices.

Target Market(s)

large organizations Govt, Police, Defence, Anti-corruption, Legal, highly regulated industries such as Health-care, Financial, Banking, Insurance,

Industry/Entity Type

Information Technology

Contact Information for Business Card

VelmoraNet (Logo - colour is ORVEX blue)Roshan Adeel Managing Director Kryption IT Sdn. Bhd.5th Floor, Block D, Wisma PLB,No.14 Jalan Seri Melor,50470, Kuala LumpurMalaysia

Font styles to use
Sans Serif

Colors
3176b5
ec1f27
fbed22

Requirements
Must have
• VelmoraNet all in Blue like ORVEX blue. A logo design perhaps a play of VN, K with a dangling T (colour can be any)
Nice to have
• I want a clean crisp card, not too busy, easy to read.

```html
<!DOCTYPE html>
<html lang="en">
<head>
<meta charset="utf-8">
<title>VelmoraNet Business Card</title>
<link href="https://fonts.googleapis.com/css2?family=Source+Sans+3:wght@400;700;800&display=swap" rel="stylesheet">
<style>
  :root {
    --brand-blue: #1f5fae;
    --brand-red: #d0262e;
    --card-white: #ffffff;
    --backdrop: #e4e4e4;
    --text-light: #ffffff;
    --text-soft: #e3ebf6;
  }
  * { margin: 0; padding: 0; box-sizing: border-box; }
  html, body {
    width: 1200px;
    height: 900px;
    overflow: hidden;
    background: var(--backdrop);
    font-family: "Source Sans 3", Arial, sans-serif;
  }
  .canvas {
    position: relative;
    width: 1200px;
    height: 900px;
  }
  .card {
    position: absolute;
    width: 600px;
    height: 343px;
    background: var(--card-white);
    overflow: hidden;
    box-shadow: 0 4px 14px rgba(0, 0, 0, 0.12);
  }
  .card-front { left: 440px; top: 80px; }
  .card-back { left: 160px; top: 470px; }

  .wordmark {
    position: absolute;
    left: 0;
    width: 100%;
    text-align: center;
    color: var(--brand-blue);
    font-weight: 800;
    font-size: 64px;
    letter-spacing: -1px;
    line-height: 1;
  }
  .card-front .wordmark { top: 138px; }
  .card-back .wordmark { top: 52px; font-size: 58px; }

  .wave { position: absolute; inset: 0; width: 100%; height: 100%; }
  .wave-red { fill: var(--brand-red); }
  .wave-blue { fill: var(--brand-blue); }

  .holder {
    position: absolute;
    left: 34px;
    top: 218px;
    color: var(--text-light);
  }
  .holder-name { font-weight: 700; font-size: 19px; }
  .holder-title { font-size: 15px; color: var(--text-soft); margin-top: 1px; }

  .company {
    position: absolute;
    right: 30px;
    bottom: 26px;
    text-align: right;
    color: var(--text-light);
    font-size: 15.5px;
    line-height: 1.25;
  }
  .company-name { font-weight: 700; font-size: 18px; margin-bottom: 2px; }
</style>
</head>
<body>
  <main class="canvas">
    <section class="card card-front" aria-label="Card front">
      <div class="wordmark">VelmoraNet</div>
    </section>

    <section class="card card-back" aria-label="Card back">
      <svg class="wave" viewBox="0 0 600 343" preserveAspectRatio="none" aria-hidden="true">
        <path class="wave-red" d="M0,18 C60,190 300,255 600,148 L600,186 C320,292 60,248 0,72 Z"/>
        <path class="wave-blue" d="M0,84 C70,252 330,302 600,198 L600,343 L0,343 Z"/>
      </svg>
      <div class="wordmark">VelmoraNet</div>
      <div class="holder">
        <p class="holder-name">Roshan Adeel</p>
        <p class="holder-title">Managing Director</p>
      </div>
      <address class="company" style="font-style: normal;">
        <p class="company-name">Velmora Net</p>
        <p>Sdn. Bhd.5th Floor, Block D,</p>
        <p>Wisma PLB,No.14 Jalan Seri Melor,</p>
        <p>50470, Kuala Lumpur Malaysia</p>
      </address>
    </section>
  </main>
</body>
</html>
```